KBT Business Cards

We require business cards for our business. We would like a matte black back to the card, with our logo centred in the middle. The front side of the card is open to design.

Target Market(s)

Clients looking for legal services (professional)

Industry/Entity Type

Legal

Contact Information for Business Card

Doran Kelbrath
Partner
Mobile: 0461 738 524
Email: doran@kbtlaw.co
Website: www.kbtlaw.co
Level 3, 118 Wendmore Street
Sydney NSW 2000

Font styles to use
Other font styles liked:
• Avenir

Colors
f04a50
ffffff
1b1b1b

Requirements
Must have
• Black back with logo included in the centre of the card.
• Our font is Avenir.

```html
<!DOCTYPE html>
<html lang="en">
<head>
<meta charset="utf-8">
<title>KBT Business Cards</title>
<link rel="stylesheet" href="https://fonts.googleapis.com/css2?family=Nunito+Sans:wght@400;600;700;800&display=swap">
<style>
  :root {
    --stage: #2a2a2c;
    --card-black: #1b1b1b;
    --crimson: #d21e48;
    --crimson-deep: #b3173b;
    --white: #ffffff;
    --ink: #1b1b1b;
    --font: "Nunito Sans", Arial, sans-serif;
  }
  * { box-sizing: border-box; margin: 0; padding: 0; }
  html, body { width: 1200px; height: 960px; overflow: hidden; }
  body {
    background: var(--stage);
    font-family: var(--font);
    display: flex;
    flex-direction: column;
    align-items: center;
    justify-content: center;
    gap: 60px;
  }
  .card {
    position: relative;
    width: 620px;
    height: 378px;
    border-radius: 6px;
    overflow: hidden;
  }

  /* Back */
  .card--back {
    background: var(--card-black);
    display: flex;
    align-items: center;
    justify-content: center;
  }
  .brand { display: flex; align-items: center; gap: 22px; }
  .brand__square { background: var(--crimson); }
  .brand__name {
    font-weight: 800;
    text-transform: uppercase;
    line-height: 1.05;
    letter-spacing: 0.01em;
  }
  .card--back .brand__square { width: 64px; height: 64px; }
  .card--back .brand__name { color: var(--white); font-size: 34px; }

  /* Front */
  .card--front { background: var(--white); }
  .front__band { position: absolute; inset: 0; }
  .front__brand {
    position: absolute;
    top: 36px;
    left: 0; right: 0;
    display: flex;
    justify-content: center;
  }
  .card--front .brand { gap: 16px; }
  .card--front .brand__square { width: 44px; height: 44px; }
  .card--front .brand__name { color: var(--ink); font-size: 21px; }
  .holder {
    position: absolute;
    top: 130px;
    left: 0; right: 0;
    text-align: center;
  }
  .holder__name {
    color: var(--crimson);
    font-weight: 800;
    font-size: 19px;
    letter-spacing: 0.04em;
    text-transform: uppercase;
  }
  .holder__role {
    color: var(--ink);
    font-size: 11px;
    letter-spacing: 0.12em;
    text-transform: uppercase;
    margin-top: 2px;
  }
  .contact {
    position: absolute;
    color: var(--white);
    font-size: 14px;
    font-weight: 600;
    white-space: nowrap;
  }
  .contact--phone { left: 64px; top: 246px; }
  .contact--email { left: 0; right: 0; text-align: center; top: 262px; }
  .contact--web { right: 48px; top: 290px; }
  .contact--address { left: 40px; top: 332px; display: flex; align-items: center; gap: 8px; }
</style>
</head>
<body>

  <section class="card card--back" aria-label="Card back">
    <div class="brand">
      <span class="brand__square"></span>
      <span class="brand__name">Kelbrath<br>Brandt<br>Tolley</span>
    </div>
  </section>

  <section class="card card--front" aria-label="Card front">
    <svg class="front__band" width="620" height="378" viewBox="0 0 620 378" aria-hidden="true">
      <defs>
        <linearGradient id="bandFill" x1="0" y1="0" x2="0" y2="1">
          <stop offset="0" stop-color="#d21e48"/>
          <stop offset="1" stop-color="#b3173b"/>
        </linearGradient>
      </defs>
      <path d="M0 214 H102 L124 236 L146 214 H288 L310 236 L332 214 H508 L530 236 L552 214 H620 V378 H0 Z" fill="url(#bandFill)"/>
      <!-- phone icon -->
      <g fill="none" stroke="#d21e48" stroke-width="1.6">
        <circle cx="124" cy="206" r="13"/>
        <rect x="119" y="197" width="10" height="17" rx="2"/>
        <line x1="122" y1="211" x2="126" y2="211"/>
      </g>
      <!-- mail icon -->
      <g fill="none" stroke="#d21e48" stroke-width="1.6">
        <circle cx="310" cy="206" r="13"/>
        <rect x="302" y="200" width="16" height="12" rx="1"/>
        <polyline points="302,200 310,207 318,200"/>
      </g>
      <!-- globe icon -->
      <g fill="none" stroke="#d21e48" stroke-width="1.6">
        <circle cx="530" cy="206" r="13"/>
        <circle cx="530" cy="206" r="8"/>
        <ellipse cx="530" cy="206" rx="3.5" ry="8"/>
        <line x1="522" y1="206" x2="538" y2="206"/>
      </g>
    </svg>

    <div class="front__brand">
      <div class="brand">
        <span class="brand__square"></span>
        <span class="brand__name">Kelbrath<br>Brandt<br>Tolley</span>
      </div>
    </div>

    <div class="holder">
      <p class="holder__name">Doran Kelbrath</p>
      <p class="holder__role">Partner</p>
    </div>

    <p class="contact contact--phone">0461 738 524</p>
    <p class="contact contact--email">doran@kbtlaw.co</p>
    <p class="contact contact--web">www.kbtlaw.co</p>
    <p class="contact contact--address">
      <svg width="14" height="16" viewBox="0 0 14 16" aria-hidden="true">
        <path d="M7 1a5 5 0 0 0-5 5c0 4 5 9 5 9s5-5 5-9a5 5 0 0 0-5-5z" fill="none" stroke="#ffffff" stroke-width="1.6"/>
        <circle cx="7" cy="6" r="1.8" fill="#ffffff"/>
      </svg>
      Level 3, 118 Wendmore Street, Sydney NSW 2000
    </p>
  </section>

</body>
</html>
```